Oil Field Service company needs professional business cards

Looking to clean up our current company business cards and look a little more professional. Brenwick Casing Services is a US based company that services the oil field. We deal with engineers, managers and oil rigs....................................................................................................................................................................................................................................................................................................................................................................................................

Target Market(s)

Oil and Gas professionals

Industry/Entity Type

Oil And Gas

Contact Information for Business Card

See attached photo as example

Font styles to use
Sans Serif

Colors
ec1f27

Requirements
Must have
• Company Logo, Name, Title, Cell, Office, Fax, Email.
• See attached photo
Nice to have
• External CRT, Internal CRT, Casing Crews, Torque Turn, Laydown Machine
Should not have
• Do not introduce any new pictures and keep it professional looking

```html
<!DOCTYPE html>
<html lang="en">
<head>
<meta charset="utf-8">
<title>Brenwick Casing Services — Business Cards</title>
<link href="https://fonts.googleapis.com/css2?family=Source+Sans+3:wght@400;600;700&display=swap" rel="stylesheet">
<style>
  :root {
    --brand-red: #ec1f27;
    --card-black: #0d0d0e;
    --card-black-soft: #1b1b1d;
    --slate: #4a5663;
    --slate-text: #5a6672;
    --paper: #ffffff;
    --backdrop: #e6e4e0;
  }
  * { box-sizing: border-box; margin: 0; padding: 0; }
  html, body {
    width: 1200px; height: 900px; overflow: hidden;
    background: var(--backdrop);
    font-family: "Source Sans 3", sans-serif;
  }
  .sheet {
    width: 1200px; height: 900px;
    display: flex; flex-direction: column; align-items: center; justify-content: center;
    gap: 40px;
  }
  .card {
    position: relative;
    width: 620px; height: 354px;
    background: radial-gradient(ellipse at 50% 40%, var(--card-black-soft), var(--card-black) 75%);
    overflow: hidden;
    box-shadow: 0 6px 18px rgba(0,0,0,0.18);
  }

  /* Company wordmark */
  .wordmark {
    display: flex; align-items: center; gap: 12px;
    color: var(--slate-text);
    font-weight: 700;
    text-transform: uppercase;
    line-height: 1;
  }
  .wordmark-dot {
    width: 18px; height: 18px; border-radius: 50%;
    background: var(--brand-red); flex: none;
  }

  /* Services side */
  .card-services .wordmark {
    position: absolute; left: 0; right: 0; top: 118px;
    justify-content: center;
    font-size: 34px; letter-spacing: 2px;
  }
  .service-list {
    position: absolute; left: 0; right: 0; top: 210px;
    list-style: none;
    display: flex; flex-wrap: wrap; justify-content: center;
    column-gap: 26px; row-gap: 10px;
    padding: 0 90px;
    color: var(--paper); font-size: 17px;
  }
  .service-list li { display: flex; align-items: center; gap: 9px; }
  .service-list li::before {
    content: ""; width: 7px; height: 7px; border-radius: 50%;
    background: var(--brand-red);
  }

  /* Contact side */
  .card-contact .wordmark {
    position: absolute; right: 34px; top: 42px;
    font-size: 22px; letter-spacing: 1.5px;
  }
  .card-contact .wordmark-dot { width: 13px; height: 13px; }
  .person { position: absolute; left: 42px; top: 32px; }
  .person-name { color: var(--brand-red); font-size: 24px; font-weight: 600; }
  .person-title { color: var(--paper); font-size: 17px; margin-top: 2px; }
  .contact-list {
    position: absolute; left: 42px; top: 118px;
    list-style: none; color: var(--paper); font-size: 17px;
  }
  .contact-list li { display: flex; align-items: center; gap: 9px; height: 22px; }
  .contact-icon { width: 13px; height: 13px; fill: var(--brand-red); flex: none; }
  .address {
    position: absolute; left: 42px; top: 222px;
    color: var(--paper); font-size: 18px;
  }
  .card-wave { position: absolute; inset: 0; width: 100%; height: 100%; }
</style>
</head>
<body>
<main class="sheet">

  <section class="card card-services" aria-label="Card back: services">
    <div class="wordmark"><span class="wordmark-dot"></span>Brenwick Casing Services</div>
    <ul class="service-list">
      <li>External CRT</li>
      <li>Internal CRT</li>
      <li>Casing Crews</li>
      <li>Torque Turn</li>
      <li>Laydown Machine</li>
    </ul>
  </section>

  <section class="card card-contact" aria-label="Card front: contact details">
    <svg class="card-wave" viewBox="0 0 620 354" preserveAspectRatio="none" aria-hidden="true">
      <path d="M0,300 C170,300 360,240 620,128 L620,354 L0,354 Z" fill="var(--slate)"/>
      <path d="M0,268 C150,300 330,255 520,196 C350,272 170,300 0,294 Z" fill="var(--brand-red)"/>
    </svg>

    <div class="wordmark"><span class="wordmark-dot"></span>Brenwick Casing Services</div>

    <div class="person">
      <p class="person-name">Cody Harlan</p>
      <p class="person-title">Area Manager</p>
    </div>

    <ul class="contact-list">
      <li>
        <svg class="contact-icon" viewBox="0 0 16 16" aria-hidden="true"><path d="M1 6 C1 2 15 2 15 6 L12 7 L11 5 C9 4 7 4 5 5 L4 7 Z M3 8 H13 L14 14 H2 Z"/></svg>
        (555) 014-2700
      </li>
      <li>
        <svg class="contact-icon" viewBox="0 0 16 16" aria-hidden="true"><path d="M4 1 H11 V5 H4 Z M1 6 H15 V15 H1 Z M4 9 H12 V10 H4 Z"/></svg>
        (555) 014-2730
      </li>
      <li>
        <svg class="contact-icon" viewBox="0 0 16 16" aria-hidden="true"><path d="M4 0 H12 V16 H4 Z M5.5 2 V12 H10.5 V2 Z"/></svg>
        (555) 017-3496
      </li>
      <li>
        <svg class="contact-icon" viewBox="0 0 16 16" aria-hidden="true"><path d="M0 3 H16 V13 H0 Z M1 4 L8 9 L15 4 Z"/></svg>
        codyharlan@brenwickcasing.com
      </li>
    </ul>

    <p class="address">Redmond Flats, OK 73990</p>
  </section>

</main>
</body>
</html>
```